Building company buisness cards

We are looking for a sharp modern new look for our business cards.
We are a New Zealand based company that specialises in house and land packages.
We have attached a photo of the current logo and would like to see if it can be improved somehow if needed.
We are open to any colours but we have chosen green at this stage.
Feel free to change the font and make the logo smarter looking.
Play with the colours and see what looks best.

We want a card that looks so good know one will want to throw it away!

Target Market(s)

Home buyers

Industry/Entity Type

Building

Contact Information for Business Card

Derek Tolvane
0217394062
dtolvane@quillmarkhomesteads.co.nz
quillmarkhomesteads.co.nz

Font styles to use
Serif
Sans Serif

Colors

Designer to choose colors to be used in the design.

Requirements
Must have
• Logo and company name on one side, details on the other side
Nice to have
• Color codes for the original green are HEX #4a8028, RGB(74,128,40), CMYK(42,0,69,50)
• Round corners, Raised and/or spot UV

```html
<!DOCTYPE html>
<html lang="en">
<head>
<meta charset="utf-8">
<title>Quillmark Homesteads – Business Card</title>
<link rel="stylesheet" href="https://fonts.googleapis.com/css2?family=Roboto:wght@400;700&display=swap">
<style>
  :root {
    --brand-green: #4a8028;
    --brand-green-dark: #3f6f21;
    --card-white: #ffffff;
    --text-grey: #555555;
    --divider-grey: #b5b5b5;
    --backdrop: #efefef;
    --mark-tint: #dfe9d6;
  }
  * { box-sizing: border-box; margin: 0; padding: 0; }
  html, body {
    width: 1200px;
    height: 712px;
    overflow: hidden;
    background: var(--backdrop);
    font-family: "Roboto", Arial, sans-serif;
  }
  .canvas {
    position: relative;
    width: 1200px;
    height: 712px;
    display: flex;
    align-items: center;
    justify-content: center;
    gap: 48px;
  }
  .card {
    width: 500px;
    height: 286px;
    border-radius: 14px;
    box-shadow: 0 8px 22px rgba(0, 0, 0, 0.12);
    position: relative;
    overflow: hidden;
  }
  .card--details {
    background: var(--card-white);
    border-bottom: 6px solid var(--brand-green);
    display: flex;
    align-items: center;
    padding: 0 36px 0 52px;
  }
  .holder-name {
    color: var(--brand-green);
    font-weight: 700;
    font-size: 21px;
    letter-spacing: 0.3px;
    text-transform: uppercase;
    white-space: nowrap;
  }
  .divider {
    width: 1px;
    height: 62px;
    background: var(--divider-grey);
    margin: 0 18px 0 20px;
    flex-shrink: 0;
  }
  .contact-list {
    list-style: none;
    color: var(--text-grey);
    font-size: 12.5px;
    line-height: 1.45;
  }
  .card--brand {
    background: var(--brand-green);
    display: flex;
    align-items: center;
    justify-content: center;
    gap: 14px;
  }
  .brand-square {
    width: 22px;
    height: 22px;
    background: var(--mark-tint);
  }
  .brand-name {
    color: var(--mark-tint);
    font-weight: 400;
    font-size: 26px;
    letter-spacing: 3px;
    text-transform: uppercase;
  }
</style>
</head>
<body>
  <main class="canvas">
    <section class="card card--details" aria-label="Card details side">
      <h1 class="holder-name">Derek Tolvane</h1>
      <span class="divider" aria-hidden="true"></span>
      <ul class="contact-list">
        <li class="contact-phone">0217394062</li>
        <li class="contact-email">dtolvane@quillmarkhomesteads.co.nz</li>
        <li class="contact-web">quillmarkhomesteads.co.nz</li>
      </ul>
    </section>
    <section class="card card--brand" aria-label="Card brand side">
      <span class="brand-square" aria-hidden="true"></span>
      <p class="brand-name">Quillmark Homesteads</p>
    </section>
  </main>
</body>
</html>
```